Lumra Learning Web Design Project

Who We are:
Lumra Learning is education information portal/ magazine, providing information about the Chinese and International education markets. Our aim is to help school principals improve there curriculum, and parents in understanding this curriculum.

Project Brief:
The site will include education news updates, educational services, curriculum developments and overseas study. We hope the site represents the cross cultural bridge between the west and east. The site will cover both the Sciences and Arts.

Note:
The logo design competition is also underway so we only need the website design

What We want:
This competition is for Design only no coding!
Design a home page based on Template 1,2 or 3. I only need to select one.
The design of an article page.

Optional
Design a Parvex Shutters metro style splash page.

Sites We like:
http://www.qv.com.cn/tonguebridge/default.aspx
http://www.dailyuniversitybulletin.co.uk/
http://kptz.sinocraftlearn.net/

Template Explanations:
Template 1-
The main information has a dynamic sliding category view that when clicked displays the relevant info.
In addition to the main upper menu it also has a left hand sliding menu that pops out on click or gesture

Template 2-
Has limited number of Articles most of the menus are drop downs from the top menu

Template 3-
No Top menu

Target Market(s)

Teachers, principals and parents

Industry/Entity Type

Education

Requirements
Should not have
• kindergarten preschool feel

```html
<!DOCTYPE html>
<html lang="en">
<head>
<meta charset="utf-8">
<title>Lumra Learning</title>
<link href="https://fonts.googleapis.com/css2?family=Abel&family=Arimo:wght@400;700&display=swap" rel="stylesheet">
<style>
:root{
  --blue:#2d72c2;
  --blue-dark:#1f5ea8;
  --grey-band:#9b9b9b;
  --nav-bg:#ebebeb;
  --line:#d8d8d8;
  --text:#555;
  --text-dark:#333;
  --footer:#2f2f2f;
  --footer-bottom:#3b3b3b;
  --panel:#f4f4f4;
}
*{margin:0;padding:0;box-sizing:border-box}
html,body{width:818px;height:1200px;overflow:hidden}
body{position:relative;background:#fff;font-family:"Abel",sans-serif;color:var(--text)}
.abs{position:absolute}

/* header */
.logo{left:102px;top:16px;font-size:27px;color:var(--blue);letter-spacing:-0.5px}
.logo small{position:absolute;left:80px;top:31px;font-size:7px;color:#555;font-family:"Arimo",sans-serif;white-space:nowrap}
.search{left:532px;top:26px;width:184px;height:21px;border:1px solid #ccc;border-radius:11px;background:#fff;font-family:"Arimo",sans-serif}
.search .hint{position:absolute;left:9px;top:6px;font-size:6px;color:#aaa}
.search .btn{position:absolute;right:0;top:-1px;width:64px;height:21px;border:1px solid #ccc;border-radius:0 11px 11px 0;background:#f4f4f4;font-family:"Abel",sans-serif;font-size:10px;color:#555;padding:5px 0 0 8px}
.search svg{position:absolute;right:6px;top:5px}

/* nav */
.nav{left:0;top:72px;width:818px;height:30px;background:var(--nav-bg);border-top:2px solid #a5a5a5;border-bottom:1px solid #ccc}
.nav a{position:absolute;top:0;height:28px;line-height:28px;text-align:center;font-size:11px;color:#333;text-decoration:none;border-right:1px solid #ccc}
.nav a.active{background:var(--blue);color:#fff;top:-3px;height:33px;line-height:34px;border:none}

/* left side */
.side{left:0;top:100px;width:102px;height:1007px;background:#fff;box-shadow:2px 0 4px rgba(0,0,0,.15)}
.side .item{position:absolute;left:0;width:99px;text-align:center;font-size:10px;color:#555;border-bottom:1px solid #e2e2e2}
.side .item.active{background:var(--blue);color:#fff;border-top:2px solid var(--blue-dark);border-bottom:2px solid var(--blue-dark)}
.phone{left:8px;top:520px;width:85px;height:157px;border-radius:12px;background:#333;border:2px solid #999}
.phone .screen{position:absolute;left:5px;top:20px;width:71px;height:110px;background:#222;color:#ddd;font-size:9.5px;text-align:center;line-height:13px;padding-top:14px}
.phone .screen b{display:block;font-weight:400;color:var(--blue);font-size:11px;margin-top:2px}
.phone .screen i{display:block;font-style:normal;font-size:5px;color:#aaa;line-height:6px}
.phone .home{position:absolute;left:35px;bottom:7px;width:11px;height:11px;border:1px solid #777;border-radius:50%}
.trial{left:0;top:673px;width:103px;height:85px;background:var(--blue);color:#fff;text-align:center;font-size:16px;line-height:19px;padding-top:14px}
.trial strong{font-weight:400;font-size:17px}

/* main */
.slider{left:124px;top:116px;width:425px;height:210px;background:linear-gradient(120deg,#9eb0c4,#d9dfe6 40%,#c7ad98 70%,#e6e6e8)}
.caption{left:116px;top:320px;width:442px;height:38px;background:var(--blue);color:#fff;font-size:17px;padding:9px 0 0 10px;border-bottom:3px solid var(--blue-dark)}
.dots{position:absolute;right:11px;top:15px}
.dots span{display:inline-block;width:10px;height:10px;border-radius:50%;background:#fff;margin-left:3px}
.dots span.on{background:#1b4f8d}

.h2{font-size:21px;color:var(--blue)}
.rule{height:3px;border-top:1px dashed #ddd;border-bottom:1px dashed #ddd}
.arrows{left:531px;top:380px}
.arrows span{display:inline-block;width:9px;height:9px;border-radius:50%;background:#e2e2e2;margin-left:2px}
.cats{font-size:10.5px;color:var(--text);line-height:20.5px;list-style:none}

.band{left:116px;width:442px;height:27px;color:#fff;font-size:19px;line-height:28px;padding:0 6px}
.band span{float:right}
.band.grey{background:var(--grey-band)}
.band.blue{background:var(--blue)}

.rss{left:496px;top:791px;font-size:10.5px;color:var(--blue)}
.news-img{top:832px;width:135px;height:88px}
.news-txt{top:926px;width:140px;font-size:12px;line-height:21px;color:#555}

/* right column */
.box{left:568px;width:147px;background:#fff;border:1px solid #ddd}
.fb-title{height:20px;background:#eee;font-family:"Arimo",sans-serif;font-weight:700;font-size:7px;color:#333;padding:6px 6px}
.fb-name{position:absolute;left:39px;top:27px;font-family:"Arimo",sans-serif;font-weight:700;font-size:8px;color:#3b5c9e}
.fb-like{position:absolute;left:39px;top:40px;width:29px;height:11px;border:1px solid #ccc;background:#f4f4f4;font-family:"Arimo",sans-serif;font-size:6px;color:#3b5c9e;text-align:center;line-height:9px}
.fb-sq{position:absolute;left:7px;top:27px;width:25px;height:25px;background:#5673a8}
.fb-count{position:absolute;left:6px;top:65px;font-family:"Arimo",sans-serif;font-size:6.5px;color:#333}
.avatar{position:absolute;width:32px;height:32px}
.avatar-name{position:absolute;width:34px;text-align:center;font-family:"Arimo",sans-serif;font-size:5.5px;color:#3b5c9e}
.fb-foot{position:absolute;left:7px;top:175px;font-family:"Arimo",sans-serif;font-size:5.5px;color:#3b5c9e}

.panel-h{height:46px;font-size:21px;color:var(--blue);border-bottom:3px solid #ccc}
.tweet{position:absolute;left:9px;width:128px;height:50px;font-family:"Arimo",sans-serif;font-size:6px;line-height:11.3px;color:#333}
.tweet .pic{position:absolute;left:0;top:2px;width:31px;height:31px;background:#e4e4e4}
.tweet .body{position:absolute;left:38px;top:0;width:92px}
.tweet b{font-size:6.5px}
.scroll{position:absolute;right:5px;width:2px;background:var(--blue)}

.uni{position:absolute;left:12px;width:120px;text-align:center;font-family:"Arimo",sans-serif;font-weight:700;font-size:10px;color:#1f3f7a}
.uni i{display:inline-block;width:11px;height:11px;background:#3b3b8a;vertical-align:-1px;margin-right:5px}

.ad{left:568px;top:845px;width:147px;height:152px;background:#9b9b9b;color:#fff;font-size:13px;text-align:center;line-height:152px;letter-spacing:.5px}

/* footer */
.footer{left:0;top:1007px;width:818px;height:143px;background:var(--footer);color:#fff}
.bubble{left:104px;top:1031px;width:38px;height:30px;background:#4a90d9;border-radius:3px}
.bubble2{left:118px;top:1040px;width:26px;height:22px;background:#7cc33a;border-radius:3px}
.f-h{font-size:17.5px;line-height:20px;color:#fff}
.f-p{font-size:10px;line-height:15px;color:#ddd}
.reasons{list-style:none;font-size:10.5px;line-height:19px;color:#ddd}
.reasons li::before{content:"";display:inline-block;width:4px;height:4px;background:var(--blue);margin-right:6px;vertical-align:2px}
.signup{left:354px;top:1125px;width:124px;height:24px;background:var(--blue);border-bottom:2px solid #5aa0e6;color:#fff;text-align:center;font-size:12.5px;line-height:24px}
.f-logo{left:573px;top:1023px;font-size:26px;color:var(--blue);letter-spacing:-0.5px}
.f-slogan{left:654px;top:1052px;font-size:7px;color:#666;font-family:"Arimo",sans-serif}
.follow{left:655px;top:1091px;font-size:9.5px;color:#666}
.social{left:657px;top:1113px}
.social span{display:inline-block;width:10px;height:10px;border-radius:50%;background:#777;margin-right:5px}
.bottom{left:0;top:1150px;width:818px;height:50px;background:var(--footer-bottom)}
.links{left:0;top:1160px;width:818px;text-align:center;font-size:11px;color:#fff;word-spacing:2px}
.links span{margin:0 11px}
.copy{left:0;top:1183px;width:818px;text-align:center;font-family:"Arimo",sans-serif;font-size:6.5px;color:#999;letter-spacing:.6px}
</style>
</head>
<body>

<header>
  <div class="abs logo">Lumra Learning<small>some slogan here</small></div>
  <div class="abs search">
    <span class="hint">Enter any Keywords</span>
    <span class="btn">SEARCH</span>
    <svg width="10" height="10" viewBox="0 0 10 10"><circle cx="6" cy="4" r="3" fill="none" stroke="#444" stroke-width="1.3"/><line x1="4" y1="6" x2="1" y2="9" stroke="#444" stroke-width="1.4"/></svg>
  </div>
</header>

<nav class="abs nav">
  <a class="active" style="left:102px;width:64px">HOME</a>
  <a style="left:166px;width:66px">NEWS</a>
  <a style="left:232px;width:66px">ARTS</a>
  <a style="left:298px;width:80px">SCIENCE</a>
  <a style="left:378px;width:73px">BOOKS</a>
  <a style="left:451px;width:86px">FEATURES</a>
  <a style="left:537px;width:92px">SUBSCRIBE</a>
  <a style="left:629px;width:87px;border:none">CONTACT US</a>
</nav>

<aside class="abs side">
  <div class="item" style="top:0;height:62px;line-height:66px">MENU ITEMS</div>
  <div class="item active" style="top:62px;height:71px;line-height:67px">MENU ITEMS</div>
  <div class="item" style="top:133px;height:61px;line-height:61px">MENU ITEMS</div>
  <div class="item" style="top:194px;height:65px;line-height:66px">MENU ITEMS</div>
  <div class="item" style="top:259px;height:64px;line-height:64px">MENU ITEMS</div>
  <div class="item" style="top:323px;height:64px;line-height:66px">MENU ITEMS</div>
</aside>
<div class="abs phone">
  <div class="screen">Get the<br>new app<br>available for<br>tablet &amp; phone<b>Lumra Learning</b><i>some slogan here</i></div>
  <span class="home"></span>
</div>
<div class="abs trial">FOR A<br>FREE TRIAL<br><strong>CLICK HERE</strong></div>

<main>
  <div class="abs slider" role="img" aria-label="Photo of smiling students seated at a desk while a teacher gestures"></div>
  <div class="abs caption">Lorem ipsum dolor sit amet consecutor...
    <div class="dots"><span class="on"></span><span></span><span></span><span></span></div>
  </div>

  <h2 class="abs h2" style="left:118px;top:370px">Categories</h2>
  <div class="abs arrows"><span></span><span></span></div>
  <div class="abs rule" style="left:116px;top:400px;width:442px"></div>
  <ul class="abs cats" style="left:129px;top:415px">
    <li>Arts</li><li>Biology &amp; Life Sciences</li><li>Business &amp; Management</li><li>Chemistry</li><li>CS: Artificial Intelligence</li>
  </ul>
  <ul class="abs cats" style="left:284px;top:414px">
    <li>CS: Software Engineering</li><li>CS: Systems &amp; Security</li><li>CS: Theory</li><li>Economics &amp; Finance</li><li>Education</li>
  </ul>
  <ul class="abs cats" style="left:432px;top:416px">
    <li>Energy &amp; Earth Sciences</li><li>Engineering</li><li>Food and Nutrition</li><li>Health &amp; Society</li><li>Humanities</li>
  </ul>
  <div class="abs rule" style="left:116px;top:525px;width:442px"></div>
  <ul class="abs cats" style="left:129px;top:538px">
    <li>Physical &amp; Earth Sciences</li><li>Physics</li><li>Social Sciences</li><li>Statistics and Data Analysis</li><li style="line-height:14px;padding-top:3px">Teacher Professional<br>Development</li>
  </ul>
  <ul class="abs cats" style="left:286px;top:537px">
    <li>Information, Tech &amp; Design</li><li>Law</li><li>Mathematics</li><li>Medicine</li><li>Music, Film, and Audio</li>
  </ul>
  <div class="abs rule" style="left:116px;top:657px;width:442px"></div>

  <div class="abs band grey" style="top:672px">EUROPE<span>DRAMA</span></div>
  <div class="abs band blue" style="top:702px">ASIA<span>SCIENCE</span></div>
  <div class="abs band grey" style="top:731px">USA<span>ENGLISH</span></div>

  <h2 class="abs h2" style="left:118px;top:780px">Recent News</h2>
  <div class="abs rss">
    <svg width="12" height="12" viewBox="0 0 12 12" style="vertical-align:-2px;margin-right:3px"><circle cx="2" cy="10" r="1.6" fill="#f08a1c"/><path d="M1 5a6 6 0 0 1 6 6M1 1a10 10 0 0 1 10 10" fill="none" stroke="#f08a1c" stroke-width="1.8"/></svg>View Blog
  </div>
  <div class="abs rule" style="left:116px;top:812px;width:442px"></div>

  <div class="abs news-img" style="left:119px;background:linear-gradient(135deg,#5a6f8a,#b48a6a 55%,#d7c2a8)" role="img" aria-label="Photo of students gathered around a laptop"></div>
  <div class="abs news-img" style="left:269px;background:linear-gradient(135deg,#8aa4b8,#d9cfa8 50%,#6a7fa0)" role="img" aria-label="Photo of a teacher helping pupils in a classroom"></div>
  <div class="abs news-img" style="left:420px;background:linear-gradient(135deg,#8aa4b8,#d9cfa8 50%,#6a7fa0)" role="img" aria-label="Photo of a classroom lesson with pupils at desks"></div>
  <p class="abs news-txt" style="left:118px">The Lumra Learning:<br>supporting Education for<br>Everyone</p>
  <p class="abs news-txt" style="left:268px">The Lumra Learning:<br>supporting Education for<br>Everyone</p>
  <p class="abs news-txt" style="left:419px">The Lumra Learning:<br>supporting Education for<br>Everyone</p>
  <div class="abs rule" style="left:116px;top:995px;width:442px"></div>
</main>

<aside>
  <section class="abs box" style="top:116px;height:186px">
    <div class="fb-title">Find us on Chatterly</div>
    <span class="fb-sq"></span>
    <span class="fb-name">Chatterly Platform</span>
    <span class="fb-like">Like</span>
    <span class="fb-count">2,147,179 people like <b>Chatterly Platform.</b></span>
    <div class="avatar" style="left:7px;top:77px;background:#dfe3ea" role="img" aria-label="Member photo"></div>
    <div class="avatar" style="left:42px;top:77px;background:#4a5666" role="img" aria-label="Member photo"></div>
    <div class="avatar" style="left:77px;top:77px;background:#a88e7c" role="img" aria-label="Member photo"></div>
    <div class="avatar" style="left:112px;top:77px;background:#6a6a72" role="img" aria-label="Member photo"></div>
    <span class="avatar-name" style="left:6px;top:110px">Rasa</span>
    <span class="avatar-name" style="left:41px;top:110px">Oren</span>
    <span class="avatar-name" style="left:76px;top:110px">Pia</span>
    <span class="avatar-name" style="left:111px;top:110px">Tavi</span>
    <div class="avatar" style="left:7px;top:124px;background:#6e6a6a" role="img" aria-label="Member photo"></div>
    <div class="avatar" style="left:42px;top:124px;background:#9a7a5a" role="img" aria-label="Member photo"></div>
    <div class="avatar" style="left:77px;top:124px;background:#2e3440" role="img" aria-label="Member photo"></div>
    <div class="avatar" style="left:112px;top:124px;background:#2c4a38" role="img" aria-label="Member photo"></div>
    <span class="avatar-name" style="left:6px;top:157px">Rasi</span>
    <span class="avatar-name" style="left:41px;top:157px">Nell</span>
    <span class="avatar-name" style="left:76px;top:157px">Ivo</span>
    <span class="avatar-name" style="left:111px;top:157px">Jarek</span>
    <span class="fb-foot">Chatterly social plugin</span>
  </section>

  <section class="abs box" style="top:311px;height:235px">
    <div class="panel-h" style="padding:13px 0 0 52px">
      <span class="abs" style="left:12px;top:10px;width:26px;height:26px;border-radius:50%;background:#4a94dd"></span>Chirps
    </div>
    <div class="tweet" style="top:62px"><span class="pic"></span><div class="body"><b>Miraholt</b> :<br>Lorem ipsum dolor sit amet consecutor. Lorem ipsum.<br>Wed,22 Apr 2013 22 : 33 : 08</div></div>
    <div class="tweet" style="top:118px"><span class="pic"></span><div class="body"><b>Miraholt</b> :<br>Lorem ipsum dolor sit amet consecutor. Lorem ipsum.<br>Wed,22 Apr 2013 22 : 33 : 08</div></div>
    <div class="tweet" style="top:174px"><span class="pic"></span><div class="body"><b>Miraholt</b> :<br>Lorem ipsum dolor sit amet consecutor. Lorem ipsum.<br>Wed,22 Apr 2013 22 : 33 : 08</div></div>
    <span class="scroll" style="top:92px;height:110px"></span>
  </section>

  <section class="abs box" style="top:552px;height:281px">
    <div class="panel-h" style="padding:13px 0 0 12px">Featured Jobs</div>
    <div class="uni" style="top:68px"><i></i>Harrowmere University</div>
    <div class="uni" style="top:112px"><i></i>Eastvale University</div>
    <div class="uni" style="top:160px;line-height:14px"><i style="display:block;margin:0 auto 6px;width:16px;height:16px"></i>Southland Institute</div>
    <div class="uni" style="top:234px">Kestrel University</div>
    <span class="scroll" style="top:90px;height:175px"></span>
  </section>

  <div class="abs ad">Advertisement</div>
</aside>

<footer>
  <div class="abs footer"></div>
  <span class="abs bubble"></span><span class="abs bubble2"></span>
  <h3 class="abs f-h" style="left:162px;top:1026px;font-weight:400">Have you got an<br>opinion?</h3>
  <p class="abs f-p" style="left:105px;top:1075px;width:200px">Why not join in the debate at LL and give us your views and opinions on what matters to you!</p>
  <h3 class="abs f-h" style="left:351px;top:1026px;font-weight:400">Reasons to REGISTER</h3>
  <ul class="abs reasons" style="left:353px;top:1050px">
    <li>Lorem ipsum dolor sit amet</li><li>Lorem ipsum dolor sit amet</li><li>Lorem ipsum dolor sit amet</li>
  </ul>
  <div class="abs signup">SIGN UP NOW</div>
  <div class="abs f-logo">Lumra Learning</div>
  <div class="abs f-slogan">some slogan here</div>
  <div class="abs follow">Follow Us On</div>
  <div class="abs social"><span></span><span></span><span></span><span></span></div>
  <div class="abs bottom"></div>
  <div class="abs links"><span>HOW TO ADVERTISE</span><span>TERMS &amp; CONDITIONS</span><span>PRIVACY POLICY</span><span>FEEDBACK</span><span>COOKIE POLICY</span><span>HELP</span></div>
  <div class="abs copy">COPYRIGHT © 2013 Lumra Learning. All Rights Reserved</div>
</footer>

</body>
</html>
```